Trifold Leaflet - Osteopathy

Trifold Leaflet (A4 size paper) to provide information and promote an established English seafront osteopathy clinic.
I would like a simple modern design to reflect the seafront location and the caring nature of osteopathy treatment. The design needs to be not be generic or too corporate.
At the top of the front page in a large font should be the word "Osteopathy" as it will be displayed in a rack of leaflets (photo attached) and needs to be eye-catching.
I have attached a logo file and some examples of the kinds of designs that I like- but i'm very open to your expert ideas!
Also attached is a photo of the location- a bit of an ugly building but right on the beach, it would be great if this location could be emphasized!
The Word files: Leaflets word-inside.doc & Leaflets word-outside.doc uploaded show the content that I'd like- this is definitely not set in stone and I appreciate that less content is probably needed. Feel free to include/leave out whatever you feel is right.
More info on the practice can be found on my website:
www.marlowbayosteo.com
The pixelharbor images are ones that I have previously bought the rights to use, but only use them if you think they suit you design- I have included them i case they are of use to you.
Target Market(s)
Any adult.
Industry/Entity Type
Building
Look and feel

```html
<!DOCTYPE html>
<html lang="en">
<head>
<meta charset="utf-8">
<title>Marlow Bay Osteopathy – Trifold Leaflet</title>
<link rel="stylesheet" href="https://fonts.googleapis.com/css2?family=Montserrat:wght@400;600;700;800&family=Questrial&display=swap">
<style>
  :root{
    --page:#e6e6e6;
    --ink:#1d1d1d;
    --ink-soft:#3a3a3a;
    --grey-dark:#5b5b5b;
    --grey-mid:#7d7d7d;
    --grey-light:#a9a9a9;
    --paper-cool:#dfe3e8;
    --white:#ffffff;
    --accent:#d4574a;
    --skin-light:#e2c2ac;
    --skin-dark:#b98a6c;
    --muscle:#b9554a;
  }
  *{box-sizing:border-box;margin:0;padding:0}
  html,body{width:1200px;height:1000px;overflow:hidden}
  body{background:var(--page);font-family:"Questrial",Arial,sans-serif;color:var(--ink)}

  .leaflet{position:absolute;left:30px;top:96px;width:1140px;height:808px;display:flex;box-shadow:0 6px 24px rgba(0,0,0,.18)}
  .panel{position:relative;width:380px;height:808px;overflow:hidden}
  .panel + .panel{border-left:1px solid rgba(0,0,0,.12)}
  .panel-bg{position:absolute;inset:0;width:100%;height:100%}

  /* ---------- Left panel ---------- */
  .brand{position:absolute;top:40px;right:26px;display:flex;align-items:center;gap:8px;
    font-family:"Questrial",Arial,sans-serif;font-size:17px;color:var(--grey-dark)}
  .brand-dot{width:10px;height:10px;border-radius:50%;background:var(--grey-dark)}
  .intro{position:absolute;left:24px;top:186px;width:300px;color:var(--white);font-size:13.2px;line-height:1.3;text-align:justify}
  .intro p + p{margin-top:2px}
  .tagline{position:absolute;left:30px;top:457px;width:345px;height:40px;border-radius:20px 0 0 20px;background:var(--white);
    font-family:"Montserrat",Arial,sans-serif;font-weight:700;font-size:20px;color:var(--grey-dark);
    display:flex;align-items:center;justify-content:center;white-space:nowrap}
  .treating{position:absolute;left:26px;top:530px;color:var(--white)}
  .treating h3{font-family:"Montserrat",Arial,sans-serif;font-weight:700;font-size:34px;line-height:1}
  .treating ul{list-style:none;margin-top:12px}
  .treating li{font-family:"Montserrat",Arial,sans-serif;font-weight:600;font-size:17px;height:28px;display:flex;align-items:center;white-space:nowrap}
  .treating .leader{display:inline-block;border-bottom:2px dotted var(--white);margin-left:8px;height:0;opacity:.85}
  .anatomy{position:absolute;left:250px;top:505px;width:90px;height:275px}

  /* ---------- Middle panel ---------- */
  .safe-title{position:absolute;top:34px;left:150px;width:215px;color:var(--ink)}
  .safe-title .big{font-family:"Montserrat",Arial,sans-serif;font-weight:800;font-size:27px;letter-spacing:-.5px;line-height:1;white-space:nowrap}
  .safe-title .small{font-family:"Questrial",Arial,sans-serif;color:var(--accent);font-size:18px;line-height:1.05;margin-left:4px}
  .safe-title .safe{font-family:"Questrial",Arial,sans-serif;font-size:50px;line-height:.95;letter-spacing:-1px;white-space:nowrap}
  .safe-title .amp{color:var(--accent);font-size:70px;line-height:.6;vertical-align:-4px;margin-left:-4px}
  .safe-copy{position:absolute;top:160px;left:150px;width:205px;color:var(--grey-dark);font-size:11.5px;line-height:1.22}
  .recommend{position:absolute;top:490px;left:24px;width:340px;color:var(--white)}
  .recommend .kicker{font-size:18px;line-height:1.2}
  .recommend h2{font-family:"Montserrat",Arial,sans-serif;font-weight:700;font-size:22px;line-height:1.2;margin-top:4px;white-space:nowrap}
  .recommend-copy{position:absolute;top:560px;left:24px;width:240px;color:var(--white);font-size:11.4px;line-height:1.24;text-align:justify}
  .badge-square{position:absolute;top:570px;left:280px;width:68px;height:68px;background:#24385c;border:2px solid var(--white)}
  .badge-small{position:absolute;top:714px;width:40px;height:44px;border:2px solid var(--ink-soft);border-radius:4px}
  .badge-oval{position:absolute;top:714px;left:148px;width:86px;height:44px;border:2px solid var(--ink-soft);border-radius:50%}

  /* ---------- Right panel ---------- */
  .treatment-photo{position:absolute;left:151px;top:36px;width:184px;height:184px;border-radius:50%;border:8px solid #cfcfcf}
  .visit-title{position:absolute;left:18px;top:222px;font-family:"Questrial",Arial,sans-serif;font-size:40px;line-height:1.05;color:var(--ink);font-weight:400}
  .visit-title strong{font-family:"Montserrat",Arial,sans-serif;font-weight:800}
  .visit-steps{position:absolute;left:18px;top:338px;width:345px;color:var(--ink)}
  .visit-steps h4{font-family:"Montserrat",Arial,sans-serif;font-weight:600;font-size:17px;line-height:1.1}
  .visit-steps p{font-family:"Montserrat",Arial,sans-serif;font-weight:600;font-size:11.3px;line-height:1.2;text-align:justify;margin-bottom:14px}
  .cta{position:absolute;left:26px;bottom:0;width:354px;height:88px;background:var(--accent);border-radius:16px 0 0 0;color:var(--white);padding:14px 0 0 22px}
  .cta .line1{font-family:"Montserrat",Arial,sans-serif;font-weight:600;font-size:17px;letter-spacing:1.5px;line-height:1}
  .cta .line2{font-size:13px;letter-spacing:1px;margin-top:2px}
  .cta .phone{display:flex;align-items:center;gap:8px;margin-top:8px;font-family:"Montserrat",Arial,sans-serif;font-weight:700;font-size:21px;letter-spacing:1.5px;white-space:nowrap}
  .cta .phone small{font-size:15px;letter-spacing:2px}
</style>
</head>
<body>
<main class="leaflet">

  <!-- Left panel -->
  <section class="panel panel-left">
    <svg class="panel-bg" viewBox="0 0 380 808" preserveAspectRatio="none" aria-hidden="true">
      <defs>
        <linearGradient id="leftLower" x1="0" y1="0" x2="0" y2="1">
          <stop offset="0" stop-color="#8a8a8a"/><stop offset="1" stop-color="#5a5a5a"/>
        </linearGradient>
      </defs>
      <rect width="380" height="808" fill="url(#leftLower)"/>
    </svg>
    <div role="img" aria-label="Photograph of an arm and shoulder being gently stretched" style="position:absolute;left:0;top:0;width:380px;height:470px;background:linear-gradient(160deg,#dfe4ea 0%,#dfe4ea 30%,var(--skin-light) 55%,var(--skin-dark) 100%)"></div>
    <svg class="panel-bg" viewBox="0 0 380 808" preserveAspectRatio="none" aria-hidden="true">
      <polygon points="0,180 330,164 378,440 0,440" fill="#5c5c5c"/>
      <polygon points="0,440 378,440 380,808 0,808" fill="url(#leftLower)"/>
    </svg>
    <div class="brand"><span class="brand-dot"></span>Marlow Bay Osteopathy</div>
    <div class="intro">
      <p>Much of the pain and disability we suffer stems from abnormalities in our body's structure and function. Osteopathy treats problems related to the musculoskeletal system, muscles, ligaments, nerves and joints, and helps the body's natural healing ability to correct itself and relieve the pain caused by dysfunction.</p>
      <p>When the body is balanced and efficient, just like a tuned engine, it will function with minimum wear and tear, requiring less energy to operate correctly.</p>
    </div>
    <div class="tagline">Natural, Drug Free, Pain Relief</div>
    <div class="treating">
      <h3>Treating:</h3>
      <ul>
        <li>Back &amp; Neck Pain<span class="leader" style="width:52px"></span></li>
        <li>Arthritis &amp; Joint Pain<span class="leader" style="width:30px"></span></li>
        <li>Frozen Shoulder<span class="leader" style="width:66px"></span></li>
        <li>Sciatica<span class="leader" style="width:132px"></span></li>
        <li>Sports Injury<span class="leader" style="width:92px"></span></li>
      </ul>
    </div>
    <div class="anatomy" role="img" aria-label="Illustration of the human muscular system seen from behind, with pain points highlighted" style="background:linear-gradient(180deg,#c46a5c 0%,var(--muscle) 60%,#8e3e36 100%);border-radius:40px 40px 14px 14px;opacity:.9"></div>
  </section>

  <!-- Middle panel -->
  <section class="panel panel-middle">
    <div role="img" aria-label="Photograph of hands supporting a bent knee during treatment" style="position:absolute;left:0;top:0;width:380px;height:490px;background:linear-gradient(150deg,#dfe3e8 0%,var(--skin-light) 40%,var(--skin-dark) 85%,#a07760 100%)"></div>
    <svg class="panel-bg" viewBox="0 0 380 808" preserveAspectRatio="none" aria-hidden="true">
      <defs>
        <linearGradient id="midLower" x1="0" y1="0" x2="0" y2="1">
          <stop offset="0" stop-color="#8c8c8c"/><stop offset="1" stop-color="#9a9a9a"/>
        </linearGradient>
      </defs>
      <polygon points="0,470 230,482 380,388 380,808 0,808" fill="url(#midLower)"/>
    </svg>
    <div class="safe-title">
      <div class="big">OSTEOPATHY</div>
      <div class="small">is Regulated</div>
      <div class="safe">SAFE<span class="amp">&amp;</span></div>
    </div>
    <p class="safe-copy">Osteopathy is one of only two complementary and alternative medicines (CAMs) that are regulated under UK law. This regulation works in much the same way as regulation for medical doctors.</p>
    <div class="recommend">
      <div class="kicker">As Recommended by</div>
      <h2>The Guild of Family GP's</h2>
    </div>
    <p class="recommend-copy">Osteopathy is used to treat many problems related to the musculoskeletal system. Osteopathic manipulation has been recommended by The National Council for Care Standards (NCCS) and The Guild of Family Practitioners (GFP) for the treatment of low back pain.</p>
    <div class="badge-square" aria-hidden="true"></div>
    <div class="badge-small" style="left:88px" aria-hidden="true"></div>
    <div class="badge-oval" aria-hidden="true"></div>
  </section>

  <!-- Right panel -->
  <section class="panel panel-right">
    <svg class="panel-bg" viewBox="0 0 380 808" preserveAspectRatio="none" aria-hidden="true">
      <defs>
        <linearGradient id="rightTop" x1="0" y1="0" x2="0" y2="1">
          <stop offset="0" stop-color="#dfe3e8"/><stop offset="1" stop-color="#c9ccd0"/>
        </linearGradient>
        <linearGradient id="rightLower" x1="0" y1="0" x2="0" y2="1">
          <stop offset="0" stop-color="#8e8e8e"/><stop offset="1" stop-color="#a4a4a4"/>
        </linearGradient>
      </defs>
      <rect width="380" height="808" fill="url(#rightTop)"/>
      <polygon points="250,250 380,150 380,300" fill="#4a4a4a"/>
      <polygon points="0,330 380,250 380,808 0,808" fill="url(#rightLower)"/>
    </svg>
    <div class="treatment-photo" role="img" aria-label="Photograph of hands treating a patient's shoulder" style="background:radial-gradient(circle at 40% 45%,var(--skin-light) 0%,var(--skin-dark) 60%,#6e6e6e 100%)"></div>
    <h2 class="visit-title">Your first<br><strong>visit</strong></h2>
    <div class="visit-steps">
      <h4>Medical History</h4>
      <p>On your first visit, we will ask you lots of questions to build up a detailed medical history. Your past medical history can often be relevant to current problems you are experiencing and may be discussed. We may ask about past illnesses, operations, injuries, accidents and medications.</p>
      <h4>Assessment</h4>
      <p>Based on your medical history, we will carry out some tests to help form a diagnosis of your current condition. Typical tests include posture and quality of joint movements, reflexes, palpation, muscle tone and strength, and blood pressure.</p>
      <h4>Treatment</h4>
      <p>Supported by an in depth knowledge of functional anatomy and physiology, a detailed examination enables the osteopath to diagnose safely and choose the right treatment to address the cause of the patient's symptoms. Treatment involves gentle manual techniques – easing pain, reducing swelling and improving mobility.</p>
    </div>
    <div class="cta">
      <div class="line1">For further information</div>
      <div class="line2">or if you have any questions</div>
      <div class="phone">
        <small>CALL</small>
        <svg width="22" height="22" viewBox="0 0 24 24" aria-hidden="true"><circle cx="12" cy="12" r="10.5" fill="none" stroke="#fff" stroke-width="2"/><path d="M9 6.5l1.6 2.6-1.1 1.3c.6 1.5 1.7 2.6 3.1 3.2l1.3-1.1 2.6 1.6-.8 2.1c-4 .2-8.2-4-8-8z" fill="#fff"/></svg>
        01632 960 418
      </div>
    </div>
  </section>

</main>
</body>
</html>
```